Elegant Business Card for Technology Company

Client is a supplier of innovative industrial communications and automation equipment since 2002. This contest is to gather fresh ideas for a redesign of the existing business card. Client is looking for design that best communicates tagline "Industrial Networking and Computing Specialist".

Design submissions should look modern, clean, elegant and professional. It should not be cluttered. Use white as the primary colour. Orange and black as secondary colour. Refer to jpeg File 1 on the current design.

Fonts used by Client used include Arial Regular, Arial Black, Roboto Regular, Roboto Black and Lato.

The winning design will be sent for offset printing using super white 250gsm artcard paper (open for suggestions).

Target Market(s)

System Engineers, Project Managers, Purchasing Managers from companies providing engineering services for Smart Cities.

Industry/Entity Type

Information Technology

Contact Information for Business Card

Refer to PDF File 3 for Business Card Details. Priority of short contact information would be as follows Name > Job Title > Email > Mobile > Web > Tel > Fax > Business Address >UEN (UEN represents company registration number)

Font styles to use
Sans Serif

Colors
ffffff
f37122
000000
5c5c5c

Requirements
Must have
• Refer to AI File 2 (Company Logo) & PDF File 3 (Information on Namecard)
Should not have
• No QR codes
• No Social Media Icons
• Do not create full Black or Orange colour background

```html
<!DOCTYPE html>
<html lang="en">
<head>
<meta charset="utf-8">
<title>VANTREL Business Card</title>
<link rel="stylesheet" href="https://fonts.googleapis.com/css2?family=Open+Sans:wght@400;600;700&display=swap">
<style>
  :root {
    --orange: #f37122;
    --black: #000000;
    --grey: #5c5c5c;
    --white: #ffffff;
    --backdrop: #eeeeee;
  }
  * { margin: 0; padding: 0; box-sizing: border-box; }
  html, body {
    width: 1105px; height: 1200px; overflow: hidden;
    background: var(--backdrop);
    font-family: "Open Sans", Arial, sans-serif;
  }
  .card {
    position: absolute; left: 182px; width: 746px; height: 426px;
    background: var(--white); color: var(--grey);
  }
  .card-front { top: 120px; }
  .card-back { top: 636px; border-bottom: 10px solid var(--orange); }

  .brand {
    position: absolute; left: 0; right: 0;
    display: flex; align-items: center; justify-content: center; gap: 18px;
  }
  .card-front .brand { top: 112px; }
  .card-back .brand { top: 122px; }
  .brand-dot { width: 64px; height: 64px; border-radius: 50%; background: var(--orange); }
  .brand-name {
    font-weight: 700; font-size: 60px; letter-spacing: 2px; line-height: 1;
    color: var(--black);
  }

  .name-rule {
    position: absolute; top: 250px; left: 50px; right: 48px;
    display: flex; align-items: center; gap: 8px;
  }
  .name-rule .rule { flex: 1; height: 1.5px; background: var(--orange); }
  .person-name { color: var(--orange); font-size: 24px; font-weight: 600; white-space: nowrap; }
  .person-title { color: var(--black); font-size: 19px; white-space: nowrap; }

  .contact-list {
    position: absolute; top: 284px; left: 48px; list-style: none;
    font-size: 19px; line-height: 28px; color: var(--grey);
  }
  .contact-list li { display: flex; align-items: center; gap: 12px; }
  .contact-list svg { width: 17px; height: 17px; fill: var(--orange); flex: none; }

  .address {
    position: absolute; top: 286px; right: 42px; text-align: right;
    font-style: normal; font-size: 19px; line-height: 27px; color: var(--grey);
  }
  .web { color: var(--orange); letter-spacing: 1.5px; }

  .tagline-list {
    position: absolute; top: 290px; left: 0; right: 0; list-style: none;
    text-align: center; font-size: 20px; line-height: 26.5px; color: var(--grey);
  }
  .tagline-list .tagline-lead { color: var(--orange); }
</style>
</head>
<body>
  <section class="card card-front" aria-label="Business card front">
    <div class="brand">
      <span class="brand-dot"></span>
      <span class="brand-name">VANTREL</span>
    </div>

    <div class="name-rule">
      <span class="rule"></span>
      <span class="person-name">Daniel Koh -</span>
      <span class="person-title">Sales Manager</span>
      <span class="rule"></span>
    </div>

    <ul class="contact-list">
      <li>
        <svg viewBox="0 0 24 24" aria-hidden="true"><path d="M6.6 10.8a15.1 15.1 0 0 0 6.6 6.6l2.2-2.2c.3-.3.7-.4 1-.2 1.1.4 2.3.6 3.6.6.6 0 1 .4 1 1V20c0 .6-.4 1-1 1A17 17 0 0 1 3 4c0-.6.4-1 1-1h3.5c.6 0 1 .4 1 1 0 1.3.2 2.5.6 3.6.1.3 0 .7-.2 1z"/></svg>
        <span>+65 6100 2040</span>
      </li>
      <li>
        <svg viewBox="0 0 24 24" aria-hidden="true"><path d="M7 1h10a2 2 0 0 1 2 2v18a2 2 0 0 1-2 2H7a2 2 0 0 1-2-2V3a2 2 0 0 1 2-2zm0 3v14h10V4zm5 15.2a1.2 1.2 0 1 0 0 2.4 1.2 1.2 0 0 0 0-2.4z"/></svg>
        <span>+65 9000 1234</span>
      </li>
      <li>
        <svg viewBox="0 0 24 24" aria-hidden="true"><path d="M6 2h12v5H6zM3 8h18a2 2 0 0 1 2 2v7h-4v5H5v-5H1v-7a2 2 0 0 1 2-2zm4 8v4h10v-4z"/></svg>
        <span>+65 6100 2041</span>
      </li>
      <li>
        <svg viewBox="0 0 24 24" aria-hidden="true"><path d="M2 5h20v14H2zm2 2v.5l8 5 8-5V7z"/></svg>
        <span>sales@vantrel.com.sg</span>
      </li>
    </ul>

    <address class="address">
      22 Kallang Way<br>
      Kallang Hub #02-15 (Lobby B)<br>
      Singapore 349120<br>
      <span class="web">www.vantrel.com.sg</span>
    </address>
  </section>

  <section class="card card-back" aria-label="Business card back">
    <div class="brand">
      <span class="brand-dot"></span>
      <span class="brand-name">VANTREL</span>
    </div>
    <ul class="tagline-list">
      <li class="tagline-lead">Industrial Networking &amp; Computing Specialist</li>
      <li>Industrial Ethernet / Wireless / Cellular</li>
      <li>Industrial &amp; Embedded Computing / Serial / Fieldbus Connectivity</li>
      <li>IP Video Surveillance / Remote Automation</li>
    </ul>
  </section>
</body>
</html>
```